Concierge Dental / Medical Supply Ordering Business - Sleek, Efficient, Professional, Elite

www.brantonkeelmedical.com - example website.

We are a concierge supply ordering business for medical and dental that provide DSO price savings on supplies while maintaining business autonomy and independence.

We want a very simple website that looks very professional says what we do and gives a very simple method to contact us & sign up as above.

Target Market(s)

Independent Dental and Medical Practices

Industry/Entity Type

Dental and Medical - healthcare

Coding

Coded - Design and coding required

Number of Pages Required

3 page

Font styles to use
Sans Serif

Colors
0054AA
0677BA
7BADD7
CADEEF
E8F1F8

Requirements
Must have
• Simple contact page, sleek efficient design, uncomplicated.
Nice to have
• Sign up page vs just a contact page.
Should not have
• Lots of pages, hard to navigate,

```html
<!DOCTYPE html>
<html lang="en">
<head>
<meta charset="utf-8">
<title>Brantonkeel Medical Supply</title>
<link href="https://fonts.googleapis.com/css2?family=Open+Sans:wght@300;400;600;700&family=Ubuntu:wght@400;500;700&display=swap" rel="stylesheet">
<style>
:root{
  --navy:#0c1f3d;
  --teal:#08a6c9;
  --dark:#1f252c;
  --dark2:#2a3038;
  --mist:#eef2f7;
  --text:#5b6370;
  --white:#ffffff;
  --line:#d5dbe3;
}
*{margin:0;padding:0;box-sizing:border-box}
html,body{width:1200px;height:4352px;overflow:hidden}
body{position:relative;font-family:"Open Sans",sans-serif;color:var(--navy);background:var(--white)}
.abs{position:absolute}
.head{font-family:"Ubuntu",sans-serif}
.band{position:absolute;left:0;width:1200px}
.ph{position:absolute}
.center{text-align:center;left:0;width:1200px}
.eyebrow{font-size:14px;color:var(--teal);letter-spacing:.3px}
.eyebrow.u{text-decoration:underline;text-underline-offset:6px}
.btn{position:absolute;background:var(--teal);color:var(--white);font-family:"Ubuntu",sans-serif;font-weight:500;font-size:16px;display:flex;align-items:center;justify-content:center;gap:16px}
.lorem{font-size:13px;line-height:21px;color:var(--text)}
/* top bar */
.topbar{top:0;height:50px;font-size:12px;color:var(--white)}
.topbar span{position:absolute;top:16px;display:flex;align-items:center;gap:6px}
.nav{left:83px;top:32px;width:1032px;height:88px;background:var(--white);border-radius:3px}
.nav a{position:absolute;top:38px;font-size:13px;color:var(--navy);text-decoration:none;letter-spacing:.3px}
.brandmark{display:flex;align-items:center;gap:8px;font-family:"Ubuntu",sans-serif;font-weight:500;color:var(--navy)}
.brandmark i{display:block;width:14px;height:14px;background:var(--teal)}
/* services */
.card{position:absolute;top:967px;width:324px;height:268px;background:var(--white);box-shadow:0 4px 16px rgba(12,31,61,.08);border-radius:4px}
.card .ph{left:18px;top:16px;width:288px;height:164px}
.card .badge{position:absolute;right:18px;top:124px;width:56px;height:56px;border-radius:50%;background:var(--navy);display:flex;align-items:center;justify-content:center}
.card .lbl{position:absolute;top:202px;width:100%;text-align:center;font-size:11px;color:var(--teal)}
.card h3{position:absolute;top:218px;width:100%;text-align:center;font-family:"Ubuntu",sans-serif;font-weight:500;font-size:27px}
/* why */
.why h4{position:absolute;font-family:"Ubuntu",sans-serif;font-weight:500;font-size:19px;color:var(--navy)}
.why p{position:absolute;font-size:12.5px;line-height:21px;color:var(--text);width:210px}
.ico{position:absolute;width:66px;height:66px;border-radius:50%;background:var(--navy);border:3px solid #fff;display:flex;align-items:center;justify-content:center}
/* testimonials */
.tcard{position:absolute;top:2905px;width:488px;height:188px;background:rgba(255,255,255,.14);border-radius:3px;color:var(--white)}
.tcard h3{position:absolute;left:22px;top:32px;font-family:"Ubuntu",sans-serif;font-weight:500;font-size:28px}
.tcard p{position:absolute;left:20px;top:80px;width:450px;font-size:14.5px;line-height:24px}
.tcard .tail{position:absolute;left:36px;bottom:-16px;width:0;height:0;border-left:14px solid transparent;border-right:14px solid transparent;border-top:16px solid rgba(255,255,255,.14)}
.person{position:absolute;color:var(--white)}
.person .av{position:absolute;left:0;top:0;width:64px;height:64px;border-radius:50%;background:linear-gradient(135deg,#c8cdd4,#5b6470)}
.person b{position:absolute;left:90px;top:12px;font-family:"Ubuntu",sans-serif;font-weight:500;font-size:21px;white-space:nowrap}
.person small{position:absolute;left:90px;top:44px;font-size:14px}
/* form */
.field{position:absolute;border:1px solid var(--line);font-size:11px;color:#8a929c;padding:8px 8px}
/* footer */
.fnav a{position:absolute;top:4114px;font-size:14px;color:var(--navy);text-decoration:none;transform:translateX(-50%);white-space:nowrap}
.fci{position:absolute;top:4211px;width:54px;height:54px;border-radius:50%;border:1.5px solid var(--navy);display:flex;align-items:center;justify-content:center}
.ftxt{position:absolute;font-size:12px;color:var(--navy);line-height:17px}
</style>
</head>
<body>

<!-- HERO -->
<section class="band" style="top:0;height:767px;">
  <div class="ph" role="img" aria-label="Office team working together at a bright modern workspace, darkened" style="left:0;top:0;width:1200px;height:767px;background:linear-gradient(120deg,#3a4048 0%,#20262d 45%,#2d333b 70%,#1a1f25 100%);"></div>
  <div class="band topbar">
    <span style="left:96px"><svg width="10" height="12" viewBox="0 0 10 12"><path d="M5 0a4 4 0 0 1 4 4c0 3-4 8-4 8S1 7 1 4a4 4 0 0 1 4-4z" fill="#fff"/><circle cx="5" cy="4" r="1.5" fill="#2a3038"/></svg>1233 Some Street , City</span>
    <span style="left:360px"><svg width="13" height="9" viewBox="0 0 13 9"><rect width="13" height="9" fill="#fff"/><path d="M0 0l6.5 5L13 0" stroke="#2a3038" fill="none"/></svg>email@companysite.com</span>
    <span style="left:576px"><svg width="10" height="10" viewBox="0 0 10 10"><path d="M2 0l2 2-1 2c1 1.5 2 2.5 3 3l2-1 2 2-2 2C4 10 0 6 0 2z" fill="#fff"/></svg>123 - 123 - 1234</span>
    <span style="left:1000px;gap:12px"><i style="width:14px;height:14px;background:#fff;display:block;border-radius:2px"></i><i style="width:14px;height:14px;background:#fff;display:block;border-radius:2px"></i><i style="width:14px;height:14px;background:#fff;display:block;border-radius:2px"></i><i style="width:14px;height:14px;background:#fff;display:block;border-radius:2px"></i></span>
  </div>
  <nav class="abs nav">
    <div class="abs brandmark" style="left:46px;top:34px;font-size:15px"><i></i>Brantonkeel</div>
    <a style="left:348px">HOME</a>
    <a style="left:448px">ABOUT US</a>
    <a style="left:586px">SERVICES</a>
    <a style="left:712px">CONTACT US</a>
  </nav>
  <p class="abs center" style="top:325px;font-size:15px;font-weight:600;color:#fff">MEDICAL SUPPLY ORDERING SERVICES</p>
  <h1 class="abs center" style="top:350px;font-size:78px;line-height:88px;font-weight:400;color:#fff">Enhancing Revenue,<br>Simplifying Supply</h1>
  <a class="btn" style="left:522px;top:592px;width:156px;height:45px">Contact us
    <svg width="18" height="12" viewBox="0 0 18 12"><path d="M0 6h16M11 1l5 5-5 5" stroke="#fff" stroke-width="1.6" fill="none"/></svg></a>
</section>

<!-- SERVICES -->
<section class="band" style="top:767px;height:683px;background:var(--mist)">
  <p class="abs center eyebrow u" style="top:62px">WHAT WE DO</p>
  <h2 class="abs center head" style="top:100px;font-size:46px;font-weight:500">Services We Offer</h2>
</section>
<div class="card" style="left:85px">
  <div class="ph" role="img" aria-label="Three colleagues reviewing work at a laptop" style="background:linear-gradient(135deg,#b9c0c8,#4a525c)"></div>
  <div class="badge"><svg width="26" height="26" viewBox="0 0 24 24"><path d="M12 3l2.6 5.5 6 .8-4.4 4.1 1.1 6-5.3-2.9-5.3 2.9 1.1-6L3.4 9.3l6-.8z" stroke="#fff" stroke-width="1.4" fill="none"/></svg></div>
  <p class="lbl">OUR SERVICES</p><h3>Order Fulfillment</h3>
</div>
<div class="card" style="left:436px">
  <div class="ph" role="img" aria-label="Clasped hands resting on a table" style="background:linear-gradient(135deg,#e8e4e0,#9a8f88)"></div>
  <div class="badge"><svg width="26" height="26" viewBox="0 0 24 24"><circle cx="12" cy="12" r="8" stroke="#fff" stroke-width="1.4" fill="none"/><path d="M12 7v10M9 10h5a2 2 0 0 1 0 4H9" stroke="#fff" stroke-width="1.4" fill="none"/></svg></div>
  <p class="lbl">OUR SERVICES</p><h3>Price Savings</h3>
</div>
<div class="card" style="left:787px">
  <div class="ph" role="img" aria-label="Family relaxing together on a sofa" style="background:linear-gradient(135deg,#e6dccf,#a89580)"></div>
  <div class="badge"><svg width="26" height="26" viewBox="0 0 24 24"><path d="M5 19h14M8 19l3-7 5-2M10 8l3 3M13 4l4 4" stroke="#fff" stroke-width="1.4" fill="none"/></svg></div>
  <p class="lbl">OUR SERVICES</p><h3>Timely Delivery</h3>
</div>
<p class="abs center" style="top:1294px;font-size:18px;color:var(--text)">The demanded experts in your area</p>
<a class="btn" style="left:488px;top:1338px;width:218px;height:63px;background:#fff;color:var(--teal);font-size:23px;box-shadow:0 4px 14px rgba(12,31,61,.08)">Contact us
  <svg width="24" height="16" viewBox="0 0 24 16"><path d="M0 8h22M15 1l7 7-7 7" stroke="#08a6c9" stroke-width="2" fill="none"/></svg></a>

<!-- WHO WE ARE -->
<section class="band" style="top:1450px;height:558px">
  <div class="ph" role="img" aria-label="Darkened office scene of people working" style="left:0;top:0;width:1200px;height:558px;background:linear-gradient(110deg,#2b3138,#1c2127 55%,#30363e)"></div>
  <div class="ph" style="left:96px;top:66px;width:400px;height:370px;background:#1b3a5c;border-radius:40px;transform:rotate(-6deg)"></div>
  <div class="ph" role="img" aria-label="Two professionals reviewing a tablet in an office" style="left:112px;top:88px;width:382px;height:372px;border-radius:36px;background:linear-gradient(135deg,#c9ced4,#5d6670)"></div>
  <p class="abs" style="left:612px;top:61px;font-size:13px;color:#fff;text-decoration:underline;text-underline-offset:5px">WHO WE ARE</p>
  <h2 class="abs head" style="left:612px;top:98px;font-size:44px;line-height:51px;font-weight:500;color:#fff">The Prescription for<br>Supply Ordering.</h2>
  <h3 class="abs" style="left:612px;top:226px;font-size:21px;font-weight:400;color:#fff">Your Partner in Medical Supply Ordering</h3>
  <p class="abs" style="left:612px;top:271px;width:505px;font-size:13px;line-height:21px;color:#e4e7eb">Lorem ipsum dolor sit amet, consectetur adipiscing elit, sed do eiusmod temp or incididunt ut labore et dolore magna aliqua. Ut enim ad minim veniam, quis laboris nisi ut aliquip ex ea commodo consequat.</p>
  <p class="abs" style="left:612px;top:347px;width:505px;font-size:13px;line-height:21px;color:#e4e7eb">Lorem ipsum dolor sit amet, consectetur adipiscing elit, sed do eiusmod temp or incididunt ut labore et dolore magna aliqua.</p>
  <a class="btn" style="left:610px;top:428px;width:156px;height:45px">Contact us
    <svg width="18" height="12" viewBox="0 0 18 12"><path d="M0 6h16M11 1l5 5-5 5" stroke="#fff" stroke-width="1.6" fill="none"/></svg></a>
</section>

<!-- WHY CHOOSE US -->
<section class="why">
  <p class="abs center eyebrow u" style="top:2080px;font-size:12px">WHY US</p>
  <h2 class="abs center head" style="top:2112px;font-size:34px;font-weight:500">Why Choose Us</h2>
  <svg class="abs" style="left:432px;top:2216px" width="360" height="360" viewBox="0 0 360 360">
    <circle cx="180" cy="180" r="170" fill="none" stroke="#1b1f29" stroke-width="1.4" stroke-dasharray="5 4"/>
    <circle cx="180" cy="180" r="150" fill="none" stroke="#c9c3f0" stroke-width="10"/>
  </svg>
  <div class="ph" role="img" aria-label="Smiling businesswoman with arms crossed" style="left:477px;top:2196px;width:270px;height:335px;border-radius:0 0 135px 135px;background:linear-gradient(180deg,#d8c8b8,#2c2f3a 65%)"></div>
  <div class="ico" style="left:411px;top:2304px"><svg width="28" height="28" viewBox="0 0 24 24"><path d="M5 19h14M8 19l3-7 5-2M10 8l3 3M13 4l4 4" stroke="#fff" stroke-width="1.4" fill="none"/></svg></div>
  <div class="ico" style="left:386px;top:2404px"><svg width="28" height="28" viewBox="0 0 24 24"><circle cx="12" cy="12" r="8" stroke="#fff" stroke-width="1.4" fill="none"/><circle cx="12" cy="12" r="3" stroke="#fff" stroke-width="1.4" fill="none"/></svg></div>
  <div class="ico" style="left:428px;top:2502px"><svg width="28" height="28" viewBox="0 0 24 24"><path d="M12 3l2.6 5.5 6 .8-4.4 4.1 1.1 6-5.3-2.9-5.3 2.9 1.1-6L3.4 9.3l6-.8z" stroke="#fff" stroke-width="1.4" fill="none"/></svg></div>
  <div class="ico" style="left:729px;top:2304px"><svg width="28" height="28" viewBox="0 0 24 24"><path d="M5 19h14M8 19l3-7 5-2M10 8l3 3M13 4l4 4" stroke="#fff" stroke-width="1.4" fill="none"/></svg></div>
  <div class="ico" style="left:753px;top:2404px"><svg width="28" height="28" viewBox="0 0 24 24"><circle cx="12" cy="12" r="8" stroke="#fff" stroke-width="1.4" fill="none"/><circle cx="12" cy="12" r="3" stroke="#fff" stroke-width="1.4" fill="none"/></svg></div>
  <div class="ico" style="left:709px;top:2502px"><svg width="28" height="28" viewBox="0 0 24 24"><path d="M12 3l2.6 5.5 6 .8-4.4 4.1 1.1 6-5.3-2.9-5.3 2.9 1.1-6L3.4 9.3l6-.8z" stroke="#fff" stroke-width="1.4" fill="none"/></svg></div>

  <h4 style="left:201px;top:2299px">Cost-Effective</h4>
  <p style="left:201px;top:2330px">Lorem ipsum dolor sit amet, consectetur adipiscing elit, sed do eiusmod tempor incididunt</p>
  <h4 style="left:171px;top:2414px">Client-Centric</h4>
  <p style="left:171px;top:2445px">Lorem ipsum dolor sit amet, consectetur adipiscing elit, sed do eiusmod tempor incididunt</p>
  <h4 style="left:201px;top:2524px">Global Reach</h4>
  <p style="left:201px;top:2555px">Lorem ipsum dolor sit amet, consectetur adipiscing elit, sed do eiusmod tempor incididunt</p>
  <h4 style="left:833px;top:2280px">Regulatory Compliance</h4>
  <p style="left:833px;top:2311px">Lorem ipsum dolor sit amet, consectetur adipiscing elit, sed do eiusmod tempor incididunt</p>
  <h4 style="left:852px;top:2399px">Quality Assurance</h4>
  <p style="left:852px;top:2430px">Lorem ipsum dolor sit amet, consectetur adipiscing elit, sed do eiusmod tempor incididunt</p>
  <h4 style="left:808px;top:2524px">Timely Delivery</h4>
  <p style="left:808px;top:2555px">Lorem ipsum dolor sit amet, consectetur adipiscing elit, sed do eiusmod tempor incididunt</p>
</section>

<!-- TESTIMONIALS -->
<section class="band" style="top:2716px;height:555px">
  <div class="ph" role="img" aria-label="Darkened photo of a professional meeting" style="left:0;top:0;width:1200px;height:555px;background:linear-gradient(110deg,#3a4048,#1f242b 50%,#2e343c)"></div>
  <p class="abs" style="left:90px;top:48px;font-size:13px;color:#fff;text-decoration:underline;text-underline-offset:5px">TESTIMONIALS</p>
  <h2 class="abs head" style="left:89px;top:80px;font-size:42px;font-weight:500;color:#fff">What our clients are saying</h2>
  <p class="abs" style="left:916px;top:98px;font-size:15px;font-weight:600;color:#fff">More Testimonials</p>
  <div class="abs" style="left:1065px;top:89px;width:37px;height:38px;background:var(--teal);display:flex;align-items:center;justify-content:center"><svg width="10" height="14" viewBox="0 0 10 14"><path d="M2 1l6 6-6 6" stroke="#fff" stroke-width="2.2" fill="none"/></svg></div>
</section>
<div class="tcard" style="left:93px"><h3>Their service was excellent</h3><p>Lorem ipsum dolor sit amet, consectetur adipiscing elit, sed do eiusmod tempor incididunt ut labore et dolore magna aliqua. Ut enim ad minim</p><i class="tail"></i></div>
<div class="tcard" style="left:615px"><h3>Their service was excellent</h3><p>Lorem ipsum dolor sit amet, consectetur adipiscing elit, sed do eiusmod tempor incididunt ut labore et dolore magna aliqua. Ut enim ad minim</p><i class="tail"></i></div>
<div class="person" style="left:110px;top:3127px"><div class="av" role="img" aria-label="Client portrait"></div><b>Nora Vale</b><small>Client</small></div>
<div class="person" style="left:631px;top:3127px"><div class="av" role="img" aria-label="Client portrait"></div><b>Owen Pratt</b><small>Client</small></div>
<svg class="abs" style="left:582px;top:3230px" width="66" height="16" viewBox="0 0 66 16"><circle cx="10" cy="8" r="5.5" fill="#08a6c9"/><circle cx="31" cy="8" r="5.5" fill="#fff"/><circle cx="55" cy="8" r="5.5" fill="#fff"/></svg>

<!-- CONTACT -->
<section>
  <p class="abs center eyebrow u" style="top:3340px">CONTACT US</p>
  <h2 class="abs center head" style="top:3380px;font-size:42px;font-weight:500">Get in touch with us</h2>
  <svg class="abs" style="left:0;top:3700px" width="1200" height="300" viewBox="0 0 1200 300">
    <path d="M0 190 C40 120 100 90 150 80 L150 300 L0 300 Z" fill="#0c1f3d"/>
    <path d="M1055 110 C1120 130 1170 165 1200 200 L1200 240 C1160 205 1110 175 1055 160 Z" fill="#08a6c9"/>
  </svg>
  <div class="abs" style="left:139px;top:3495px;width:921px;height:456px;background:#fff;border-radius:14px;box-shadow:0 6px 24px rgba(12,31,61,.12);overflow:hidden">
    <div class="ph" role="img" aria-label="Smiling man holding a tablet" style="left:0;top:0;width:461px;height:456px;background:linear-gradient(135deg,#2a3440,#0f1620 60%,#34414e)"></div>
  </div>
  <div class="abs brandmark" style="left:676px;top:3530px;font-size:16px"><i></i>Brantonkeel</div>
  <h3 class="abs" style="left:650px;top:3604px;font-size:30px;font-weight:300;color:var(--navy)">Please fill out the form</h3>
  <div class="field" style="left:650px;top:3667px;width:361px;height:34px;border-width:0 0 1px 0">Name</div>
  <div class="field" style="left:650px;top:3718px;width:171px;height:37px">Phone</div>
  <div class="field" style="left:837px;top:3718px;width:174px;height:37px">Email</div>
  <div class="field" style="left:650px;top:3772px;width:361px;height:68px">Message</div>
  <a class="btn" style="left:650px;top:3857px;width:361px;height:39px;font-size:13px;font-family:'Open Sans',sans-serif;font-weight:600">Send</a>
</section>

<!-- FOOTER -->
<footer>
  <div class="abs brandmark" style="left:0;width:1200px;top:4030px;justify-content:center;font-size:22px"><i style="width:22px;height:22px"></i>Brantonkeel Supply</div>
  <div class="fnav">
    <a style="left:374px">HOME</a><a style="left:478px">SERVICES</a><a style="left:588px">ABOUT US</a><a style="left:722px">TESTIMONIALS</a><a style="left:840px">BLOG</a>
  </div>
  <div class="abs" style="left:144px;top:4168px;width:916px;height:1px;background:var(--line)"></div>
  <div class="fci" style="left:174px"><svg width="26" height="26" viewBox="0 0 24 24"><circle cx="12" cy="12" r="9" stroke="#0c1f3d" stroke-width="1.3" fill="none"/><path d="M3 12h18M12 3c3 3 3 15 0 18M12 3c-3 3-3 15 0 18" stroke="#0c1f3d" stroke-width="1.3" fill="none"/></svg></div>
  <p class="ftxt" style="left:241px;top:4222px">123, Building Name, Street<br>City, State ZY 123456</p>
  <div class="abs" style="left:431px;top:4210px;width:1px;height:56px;background:var(--line)"></div>
  <div class="fci" style="left:505px"><svg width="22" height="26" viewBox="0 0 22 26"><rect x="6" y="3" width="10" height="20" rx="2" stroke="#0c1f3d" stroke-width="1.3" fill="none"/><path d="M18 9c1.5 2 1.5 6 0 8M3 9c-1.5 2-1.5 6 0 8" stroke="#0c1f3d" stroke-width="1.3" fill="none"/></svg></div>
  <p class="ftxt" style="left:573px;top:4222px;font-size:13px">PHONE<br><span style="font-size:12px">(123) 456 7890</span></p>
  <div class="abs" style="left:749px;top:4210px;width:1px;height:56px;background:var(--line)"></div>
  <div class="fci" style="left:828px"><svg width="24" height="24" viewBox="0 0 24 24"><path d="M3 10l9-6 9 6v10H3z M3 10l9 6 9-6" stroke="#0c1f3d" stroke-width="1.3" fill="none"/></svg></div>
  <p class="ftxt" style="left:896px;top:4222px;font-size:13px">EMAIL<br><span style="font-size:12px">info@company.com</span></p>
  <div class="band" style="top:4301px;height:51px;background:var(--teal)">
    <p class="abs" style="left:149px;top:16px;font-size:13px;font-weight:600;color:#fff">Brantonkeel Medical Supply</p>
    <div class="abs" style="left:946px;top:14px;display:flex;gap:10px">
      <i style="display:block;width:22px;height:22px;border:1px solid #fff"></i><i style="display:block;width:22px;height:22px;border:1px solid #fff"></i><i style="display:block;width:22px;height:22px;border:1px solid #fff"></i><i style="display:block;width:22px;height:22px;border:1px solid #fff"></i>
    </div>
  </div>
</footer>

</body>
</html>
```